Deskside Thrive Fliers and logo design

We need to design a product logo and some informational fliers for a vigour quest.
I have attached our Deskside Thrive logo - colours need to be complimentary but not the same, we would like fresh, funky but still professional. We generally communicate in a fairly casual way to reach our market. (We don't like boring)
Clear and simple - not too busy
images are good but not actual photos
Here is our website to give you an idea www.desksidethrive.co.nz
The flier is a 3 page document.
The logo is to say Vigour Quest. The challenge is based on exercise, connecting with people, giving, learning and taking notice (The 7 paths to flourishing) Once agin the logo needs to be complementary but not the same.
The Deskside thrive logo needs to be on the fliers but the vigour quest logo is separate.
Thanks very much!!

```html
<!DOCTYPE html>
<html lang="en">
<head>
<meta charset="utf-8">
<title>Vigour Quest – Values</title>
<link rel="stylesheet" href="https://fonts.googleapis.com/css2?family=Arimo:wght@400;700&display=swap">
<style>
  :root {
    --teal: #0b6d68;
    --green: #95bd55;
    --orange: #e0583a;
    --ink: #222;
    --rule: #444;
    --paper: #fff;
    --edge: #8a8a8a;
  }
  * { box-sizing: border-box; margin: 0; padding: 0; }
  html, body { width: 928px; height: 1200px; overflow: hidden; background: var(--paper); }
  body { font-family: "Arimo", Arial, sans-serif; color: var(--ink); }
  .sheet { position: relative; width: 928px; height: 1200px; overflow: hidden; border: 1px solid var(--edge); }
  .frame { position: absolute; inset: 0; }

  .brand-quest { position: absolute; left: 38px; top: 58px; display: flex; align-items: center; gap: 14px; }
  .brand-quest .mark { width: 34px; height: 34px; background: var(--green); }
  .brand-quest .name { font-weight: 700; font-size: 34px; color: var(--ink); line-height: 1; }

  .brand-host { position: absolute; left: 600px; top: 100px; font-weight: 400; font-size: 26px; line-height: 1; color: var(--ink); }

  .values-title { position: absolute; left: 46px; top: 176px; font-size: 25px; font-weight: 700; color: #fff; }
  .values-intro { position: absolute; left: 46px; top: 208px; font-size: 14.4px; color: #fff; }

  .step1 { position: absolute; left: 60px; top: 455px; width: 130px; color: #fff; }
  .step1 h2 { font-size: 17px; line-height: 21.6px; font-weight: 700; margin-bottom: 20px; }
  .step1 p { font-size: 14.4px; line-height: 17.6px; }

  .value-list { position: absolute; top: 267px; list-style: none; font-size: 13.6px; line-height: 18.35px; }
  .col-a { left: 221px; } .col-b { left: 448px; } .col-c { left: 655px; }

  .step-title { position: absolute; left: 60px; color: #fff; font-weight: 700; font-size: 23px; line-height: 24px; }
  .step2-title { top: 796px; }
  .step3-title { top: 1071px; }

  .instruction { position: absolute; left: 60px; top: 849px; width: 765px; font-size: 14.4px; line-height: 17.6px; }
  .answers { position: absolute; left: 60px; top: 911px; list-style: none; }
  .answers li { position: relative; height: 29.6px; width: 814px; font-weight: 700; font-size: 16px; }
  .answers li::after { content: ""; position: absolute; left: 21px; right: 0; top: 20px; border-bottom: 1px solid var(--rule); }

  .support { position: absolute; left: 60px; top: 1131px; font-size: 14.4px; }
</style>
</head>
<body>
<div class="sheet">
  <svg class="frame" width="928" height="1200" viewBox="0 0 928 1200" aria-hidden="true">
    <rect x="0" y="122" width="540" height="18" fill="var(--green)"/>
    <polygon points="0,152 510,152 499,174 928,174 928,238 142,238 98,274 53,238 0,238" fill="var(--teal)"/>
    <polyline points="606,0 518,168 928,168" fill="none" stroke="var(--orange)" stroke-width="5"/>
    <rect x="0" y="430" width="200" height="348" fill="var(--teal)"/>
    <rect x="204" y="258" width="672" height="516" fill="none" stroke="var(--teal)" stroke-width="8"/>
    <polygon points="0,792 480,792 534,845 0,845" fill="var(--teal)"/>
    <rect x="0" y="1100" width="928" height="100" fill="var(--green)"/>
    <rect x="36" y="1122" width="856" height="50" fill="var(--paper)"/>
    <polygon points="0,1066 508,1066 564,1122 0,1122" fill="var(--teal)"/>
  </svg>

  <div class="brand-quest"><span class="mark"></span><span class="name">Vigour Quest</span></div>
  <div class="brand-host">Deskside Thrive</div>

  <h1 class="values-title">VALUES</h1>
  <p class="values-intro">This exercise is designed to help you reach a better understanding of your most significant values.</p>

  <div class="step1">
    <h2>STEP 1:<br>What I Value<br>Most...</h2>
    <p>From this list of values (both work and personal), select the ten that are most important to you - as guides for how to behave, or as components of a valued way of life. Feel free to add any values of your own to this list.</p>
  </div>

  <ul class="value-list col-a">
    <li>Achievement</li><li>Advancement and promotion</li><li>Adventure</li><li>Affection (love and caring)</li><li>Arts</li><li>Challenging problems</li><li>Change and variety</li><li>Close relationships</li><li>Community</li><li>Competence</li><li>Competition</li><li>Cooperation</li><li>Country</li><li>Creativity</li><li>Decisiveness</li><li>Democracy</li><li>Ecological awareness</li><li>Economic security</li><li>Effectiveness</li><li>Efficiency</li><li>Ethical practice</li><li>Excellence</li><li>Excitement</li><li>Fame</li><li>Fast living</li><li>Financial gain</li><li>Freedom</li>
  </ul>
  <ul class="value-list col-b">
    <li>Friendships</li><li>Growth</li><li>Having a family</li><li>Helping other people</li><li>Helping society</li><li>Honesty</li><li>Independence</li><li>Influencing others</li><li>Inner harmony</li><li>Integrity</li><li>Intellectual status</li><li>Involvement</li><li>Job tranquility</li><li>Knowledge</li><li>Leadership</li><li>Location</li><li>Loyalty</li><li>Market position</li><li>Meaningful work</li><li>Merit</li><li>Money</li><li>Nature</li><li>Being around people who</li><li>are open and honest</li><li>Order (tranquility,</li><li>stability, conformity)</li><li>Personal development</li>
  </ul>
  <ul class="value-list col-c">
    <li>Physical challenge</li><li>Pleasure</li><li>Power and authority</li><li>Privacy</li><li>Public service</li><li>Purity</li><li>Quality of what I take part in</li><li>Quality relationships</li><li>Recognition (respect from</li><li>others, status)</li><li>Religion</li><li>Reputation</li><li>Responsibility and accountability</li><li>Security</li><li>Self-Respect</li><li>Serenity</li><li>Sophistication</li><li>Stability</li><li>Status</li><li>Supervising others</li><li>Time freedom</li><li>Truth</li><li>Wealth</li><li>Wisdom</li><li>Work under pressure</li><li>Work with others</li><li>Working alone</li>
  </ul>

  <h2 class="step-title step2-title">STEP 2:<br>ELIMINATION</h2>
  <p class="instruction">Now that you have identified ten, imagine that you are only permitted to have five values. Which five would you give up? Cross them off. Put them into order, the one that is most important to you first. Write it somewhere and refer to it when you can't make a decision, align yourself with what makes you feel good.</p>
  <ol class="answers">
    <li>1.</li><li>2.</li><li>3.</li><li>4.</li><li>5.</li>
  </ol>

  <h2 class="step-title step3-title">STEP 3:<br>SUPPORT YOURSELF</h2>
  <p class="support">Write it somewhere and refer to it when you can't make a decision, align yourself with what makes you feel good.</p>
</div>
</body>
</html>
```